Rosko Tamblin

I am a songwriter and would like to include a bio, pictures, discography, CD covers and access to some of my music

Target Market(s)

Music Lovers, songwriters publishers

Coding

Coded - Design and coding required

Number of Pages Required

5+ page

Requirements
Must have
• Pictures of my CD covers, pictures of me and either my Music or links to my music
Nice to have
Should not have
• cartoons

```html
<!DOCTYPE html>
<html lang="en">
<head>
<meta charset="utf-8">
<title>Rosko Tamblin – Songwriter</title>
<link href="https://fonts.googleapis.com/css2?family=Great+Vibes&family=Poppins:wght@400;500;600;700&family=Open+Sans:wght@400;600&display=swap" rel="stylesheet">
<style>
:root{
  --accent:#e8334a;
  --navy:#0f1a33;
  --navy-2:#16233f;
  --pink:#f3c4c7;
  --pink-soft:#fbe3e4;
  --ink:#222;
  --muted:#666;
  --white:#fff;
}
*{box-sizing:border-box;margin:0;padding:0}
html,body{width:1200px;height:3580px;overflow:hidden;background:var(--white)}
body{font-family:"Open Sans",Arial,sans-serif;color:var(--ink);position:relative}
section,header,footer{position:absolute;left:0;width:1200px}

/* hero */
.hero{top:0;height:640px;overflow:hidden}
.hero-photo{position:absolute;inset:0;background:radial-gradient(ellipse at 12% 55%,#f08a2a 0%,#b3461a 18%,#3a1a12 42%,#1a1412 70%),linear-gradient(90deg,#2a1a14,#4b3a32 60%,#2b2520)}
.hero-shade{position:absolute;inset:0;background:linear-gradient(180deg,rgba(0,0,0,.35),rgba(0,0,0,.15) 40%,rgba(0,0,0,.45))}
.nav{position:absolute;top:0;left:0;width:1200px;height:52px;display:flex;align-items:center;justify-content:space-between;padding:0 32px;background:rgba(0,0,0,.25)}
.brand{font-family:"Poppins",sans-serif;font-weight:600;font-size:22px;color:var(--white)}
.menu{display:flex;gap:30px;list-style:none}
.menu li{font-family:"Poppins",sans-serif;font-size:14px;color:var(--white)}
.menu li.active{color:var(--accent)}
.hero-name{position:absolute;left:100px;top:140px;font-family:"Great Vibes",cursive;font-size:96px;color:var(--white);font-weight:400}
.hero-line{position:absolute;left:200px;top:262px;width:380px;height:2px;background:rgba(255,255,255,.7)}
.hero-tag{position:absolute;left:110px;top:290px;width:480px;font-family:"Poppins",sans-serif;font-size:20px;line-height:1.4;color:var(--white)}
.hero-arrow{position:absolute;left:290px;top:370px;width:54px;height:54px;border:2px solid var(--white);border-radius:50%}
.hero-edge{position:absolute;left:0;bottom:0}

/* about */
.about{top:640px;height:880px}
.ghost{position:absolute;font-family:"Great Vibes",cursive;color:rgba(232,51,74,.12);white-space:nowrap}
.title{position:absolute;font-family:"Poppins",sans-serif;font-weight:600;letter-spacing:1px;color:var(--ink)}
.title span{color:var(--accent)}
.about .ghost{top:100px;left:0;width:1200px;text-align:center;font-size:130px}
.about .title{top:150px;left:0;width:1200px;text-align:center;font-size:46px}
.about-text{position:absolute;top:250px;left:140px;width:920px;text-align:center;font-size:14px;line-height:1.9;color:var(--muted)}
.about-text p+p{margin-top:22px}
.btn{position:absolute;top:430px;left:528px;width:144px;height:40px;border-radius:20px;background:var(--accent);color:var(--white);font-family:"Poppins",sans-serif;font-size:12px;font-weight:600;letter-spacing:1px;display:flex;align-items:center;justify-content:center}
.portraits{position:absolute;top:500px;left:110px;width:980px;height:360px;display:flex}
.portrait{flex:1;height:100%}
.portrait.mono{background:linear-gradient(135deg,#1d1d1d,#8a8a8a 50%,#2a2a2a)}
.portrait.warm{background:linear-gradient(160deg,#d9605a,#c96a6a 45%,#e8b3a0)}
.portrait.stone{background:linear-gradient(150deg,#b8a27a,#e2d4bc 50%,#8f7a58)}

/* discography */
.disco{top:1500px;height:1020px}
.disco-bg{position:absolute;left:0;top:0}
.disco .ghost{top:170px;left:330px;font-size:140px;color:rgba(255,255,255,.35)}
.disco .title{top:230px;left:0;width:1200px;text-align:center;font-size:44px}
.disc-art{position:absolute;top:350px;left:175px;width:260px;height:260px;border-radius:50%;border:8px solid var(--white);background:conic-gradient(#f7e4ec,#e7a1c0,#f2d6e0,#fbf2c2,#d6e4f2,#f7e4ec)}
.disco-text{position:absolute;top:350px;left:580px;width:560px;font-size:14px;line-height:1.85;color:#555}
.disco-text p+p{margin-top:26px}

/* covers */
.covers{top:2560px;height:420px}
.covers .ghost{top:-10px;left:120px;font-size:130px}
.covers .title{top:70px;left:240px;font-size:44px}
.covers-text{position:absolute;top:150px;left:130px;width:520px;text-align:center;font-size:14px;line-height:1.85;color:#555}
.cover-art{position:absolute;top:-40px;left:700px;width:320px;height:340px;background:linear-gradient(160deg,#7a4a22,#c89040 40%,#e7d2a8 60%,#6b4d2a)}

/* gallery strip */
.strip{top:2980px;height:220px;display:flex}
.strip div{flex:1;height:100%}
.s1{background:linear-gradient(160deg,#8fa3b8,#d6c8b0)}
.s2{background:linear-gradient(160deg,#2b3a4a,#d2a070)}
.s3{background:linear-gradient(160deg,#101428,#3a5aa8 60%,#e0c070)}
.s4{background:linear-gradient(160deg,#5a8fc8,#e8c050 50%,#d86a8a)}
.s5{background:linear-gradient(160deg,#1a2a5a,#c06090)}
.s6{background:linear-gradient(160deg,#e8e0d8,#a08878)}

/* footer */
.footer{top:3200px;height:380px;background:var(--navy);color:var(--white);text-align:center}
.footer-name{position:absolute;top:42px;width:1200px;font-family:"Poppins",sans-serif;font-weight:600;font-size:30px}
.footer-note{position:absolute;top:104px;width:1200px;font-size:14px;color:#d0d4e0}
.social{position:absolute;top:148px;left:541px;display:flex;gap:12px}
.social span{width:26px;height:26px;border-radius:50%;background:#2a3554}
.social span.on{background:var(--accent)}
.contact{position:absolute;top:205px;width:1200px;display:flex;justify-content:center;gap:60px;font-size:14px}
.contact div{display:flex;align-items:center;gap:12px}
.contact i{width:30px;height:30px;border-radius:50%;background:#2a3554;display:flex;align-items:center;justify-content:center}
.copy{position:absolute;bottom:0;left:0;width:1200px;height:74px;background:#0a1226;display:flex;align-items:center;justify-content:center;font-family:"Poppins",sans-serif;font-size:14px}
</style>
</head>
<body>

<header class="hero">
  <div class="hero-photo" role="img" aria-label="Photo of the songwriter in front of a glowing fire at dusk"></div>
  <div class="hero-shade"></div>
  <nav class="nav">
    <div class="brand">Rosko Tamblin</div>
    <ul class="menu">
      <li class="active">Home</li><li>About</li><li>Concert</li><li>Gallery</li><li>Blog</li><li>Contact us</li>
    </ul>
  </nav>
  <h1 class="hero-name">Rosko Tamblin</h1>
  <div class="hero-line"></div>
  <p class="hero-tag">If you are looking for superior wiring and song composition then Rosko is your guy</p>
  <div class="hero-arrow">
    <svg width="50" height="50" viewBox="0 0 50 50"><polyline points="17,21 25,29 33,21" fill="none" stroke="#fff" stroke-width="2.5"/></svg>
  </div>
  <svg class="hero-edge" width="1200" height="110" viewBox="0 0 1200 110">
    <polygon points="0,40 1200,110 0,110" fill="#fbe3e4"/>
    <polygon points="0,70 1200,110 0,110" fill="#fff"/>
  </svg>
</header>

<section class="about">
  <div class="ghost">About Me</div>
  <h2 class="title">ABOUT <span>ME</span></h2>
  <div class="about-text">
    <p>Rosko Tamblin was born and raised in a small river town, where music filled every room of the family home. He first picked up a guitar at age eight, learning old folk songs by ear from records his father kept. By his teens he was writing his own tunes and playing them at church suppers, county fairs and late night diners across the state.</p>
    <p>In high school he and two friends formed a band that toured small clubs on weekends. They performed at dances and parties, and soon cut their first record, a simple love song that still gets requests today.</p>
  </div>
  <div class="btn">LEARN MORE ›</div>
  <div class="portraits">
    <div class="portrait mono" role="img" aria-label="Black and white photo of the songwriter playing guitar"></div>
    <div class="portrait warm" role="img" aria-label="Portrait of the songwriter outdoors in a red cap"></div>
    <div class="portrait stone" role="img" aria-label="Portrait of the songwriter in a white shirt"></div>
  </div>
</section>

<section class="disco">
  <svg class="disco-bg" width="1200" height="1020" viewBox="0 0 1200 1020">
    <defs><linearGradient id="discoFill" x1="0" y1="0" x2="1" y2="1"><stop offset="0" stop-color="#f6cfd1"/><stop offset="1" stop-color="#efb6ba"/></linearGradient></defs>
    <polygon points="0,0 1200,0 1200,1020 0,1020" fill="url(#discoFill)"/>
    <polygon points="0,0 1200,0 1200,80" fill="#0f1a33"/>
    <polygon points="0,0 1200,80 1200,120 0,60" fill="#fbe3e4" opacity=".55"/>
    <polygon points="500,935 1200,935 1200,1020" fill="#0f1a33"/>
    <polygon points="0,930 1200,1020 0,1020" fill="#fff"/>
  </svg>
  <div class="ghost">Discography</div>
  <h2 class="title">DISCOGRAPHY</h2>
  <div class="disc-art" role="img" aria-label="Round album artwork in pastel pinks and yellows"></div>
  <div class="disco-text">
    <p>Lorem ipsum dolor sit amet, consectetur adipiscing elit, sed do eiusmod tempor incididunt ut labore et dolore magna aliqua. Ut enim ad minim veniam, quis nostrud exercitation ullamco laboris nisi ut aliquip ex ea commodo consequat. Duis aute irure dolor in reprehenderit in voluptate velit esse cillum dolore eu fugiat nulla pariatur.</p>
    <p>Lorem ipsum dolor sit amet, consectetur adipiscing elit, sed do eiusmod tempor incididunt ut labore et dolore magna aliqua. Ut enim ad minim veniam, quis nostrud exercitation ullamco laboris nisi ut aliquip ex ea commodo consequat. Duis aute irure dolor in reprehenderit in voluptate velit esse cillum dolore eu fugiat nulla.</p>
  </div>
</section>

<section class="covers">
  <div class="ghost">CD Covers</div>
  <h2 class="title">CD <span>COVERS</span></h2>
  <div class="covers-text">Lorem ipsum dolor sit amet, consectetur adipiscing elit, sed do eiusmod tempor incididunt ut labore et dolore magna aliqua. Ut enim ad minim veniam, quis nostrud exercitation ullamco laboris nisi ut aliquip ex ea commodo consequat. Duis aute irure dolor in reprehenderit in voluptate velit esse cillum dolore eu fugiat nulla pariatur. Excepteur sint occaecat cupidatat non proident, sunt in culpa qui officia deserunt mollit anim id est laborum. Lorem ipsum dolor sit amet, consectetur adipiscing elit, sed do eiusmod tempor incididunt ut labore et dolore magna aliqua.</div>
  <div class="cover-art" role="img" aria-label="CD cover artwork with a table scene in warm browns"></div>
</section>

<section class="strip">
  <div class="s1" role="img" aria-label="Gallery photo of a guitarist outdoors"></div>
  <div class="s2" role="img" aria-label="Gallery photo of a musician by a window"></div>
  <div class="s3" role="img" aria-label="Gallery photo of a stage with lights"></div>
  <div class="s4" role="img" aria-label="Gallery photo of a colourful performer"></div>
  <div class="s5" role="img" aria-label="Gallery photo of a concert crowd"></div>
  <div class="s6" role="img" aria-label="Gallery photo of a songwriter at home"></div>
</section>

<footer class="footer">
  <div class="footer-name">Rosko Tamblin</div>
  <p class="footer-note">From the late 50s until approximately 2011-2012, Tamblin stopped playing and writing music.</p>
  <div class="social"><span></span><span></span><span class="on"></span><span></span><span></span></div>
  <div class="contact">
    <div><i><svg width="14" height="14" viewBox="0 0 24 24"><path d="M6.6 10.8a15 15 0 0 0 6.6 6.6l2.2-2.2a1 1 0 0 1 1-.25 11 11 0 0 0 3.6.6 1 1 0 0 1 1 1V20a1 1 0 0 1-1 1A17 17 0 0 1 3 4a1 1 0 0 1 1-1h3.5a1 1 0 0 1 1 1 11 11 0 0 0 .6 3.6 1 1 0 0 1-.25 1z" fill="#fff"/></svg></i>+1 800 555 0142</div>
    <div><i><svg width="14" height="14" viewBox="0 0 24 24"><rect x="2" y="5" width="20" height="14" rx="2" fill="none" stroke="#fff" stroke-width="2"/><polyline points="2,6 12,13 22,6" fill="none" stroke="#fff" stroke-width="2"/></svg></i>hello@roskotamblin.com</div>
  </div>
  <div class="copy">© Copyrights 2020 Rosko Tamblin Music | All Rights Reserved</div>
</footer>

</body>
</html>
```